Executive Performance Review mapped on J-curve

I need to turn an executive company performance review into a visual infographic. The list of accomplishments is grouped into four calendar quarters. Each quarter needs a subtle representation of the season. The four quarters and associated list of accomplishments need to be mapped to a J-curve. - Spreadsheet with accomplishments attached (Marlowbend)- Sample image of a J-curve. You can google J-curve to see more images.- The title should be "Danica Ostrander Year in Review"

Target Market(s)

Board of Directors

Requirements
Nice to have
• This will be presented to a company founder that is an artist and customer experience expert. He is very visual so a nice visual representation of the data will be impactful. He also uses the phrase that you have to live with or work with someone for four seasons before you really know them. This is why I have the seasons mapped to the quarters. The Fall season motif should be gloomy and stormy.

```html
<!DOCTYPE html>
<html lang="en">
<head>
<meta charset="utf-8">
<title>Year in Review – Seasons on a J-Curve</title>
<link href="https://fonts.googleapis.com/css2?family=Roboto+Condensed:wght@300;400&display=swap" rel="stylesheet">
<style>
  :root{
    --summer:#e8483b;
    --fall:#9ab81f;
    --winter:#f7903a;
    --spring:#2aabb0;
    --card-bg:#f2f2f2;
    --card-line:#c9c9c9;
    --text:#3a3a3a;
    --connector:#cfcfcf;
    --curve:#444;
    --canvas:#ffffff;
  }
  html,body{margin:0;padding:0;overflow:hidden;background:var(--canvas);}
  .canvas{position:relative;width:1200px;height:754px;overflow:hidden;font-family:"Roboto Condensed","Arial Narrow",sans-serif;color:var(--text);}
  .wires{position:absolute;left:0;top:0;}
  .card{position:absolute;width:156px;background:var(--card-bg);border:1px solid var(--card-line);border-radius:7px;box-shadow:0 1px 3px rgba(0,0,0,.18);box-sizing:border-box;}
  .card-head{height:18px;line-height:19px;text-align:center;color:#fff;font-size:11px;font-weight:400;border-radius:6px 6px 0 0;margin:-1px -1px 0;}
  .card ul{margin:0;padding:4px 3px 4px 8px;list-style:none;}
  .card li{font-size:8px;font-weight:300;letter-spacing:-.3px;line-height:11.2px;position:relative;padding-left:5px;}
  .card li::before{content:"";position:absolute;left:-1px;top:5px;width:2.4px;height:2.4px;border-radius:50%;background:var(--text);}
  .summer .card-head{background:var(--summer);}
  .fall .card-head{background:var(--fall);}
  .winter .card-head{background:var(--winter);}
  .spring .card-head{background:var(--spring);}
  .season{position:absolute;border-radius:7px;color:#fff;text-align:center;box-shadow:0 1px 3px rgba(0,0,0,.2);}
  .season .name{display:block;font-size:22px;line-height:22px;padding-top:4px;}
  .season .quarter{display:block;font-size:17px;line-height:18px;}
  .season .theme{display:block;font-size:12.5px;line-height:15px;letter-spacing:.8px;}
  .season.summer{background:var(--summer);}
  .season.fall{background:var(--fall);}
  .season.winter{background:var(--winter);}
  .season.spring{background:var(--spring);}
</style>
</head>
<body>
<div class="canvas">
  <svg class="wires" width="1200" height="754" viewBox="0 0 1200 754">
    <g stroke="var(--connector)" stroke-width="1.2" fill="none">
      <line x1="401" y1="84" x2="401" y2="328"/>
      <line x1="376" y1="84" x2="401" y2="84"/>
      <line x1="207" y1="139" x2="401" y2="139"/>
      <line x1="376" y1="205" x2="401" y2="205"/>
      <line x1="207" y1="278" x2="401" y2="278"/>
      <line x1="376" y1="328" x2="401" y2="328"/>
      <line x1="402" y1="523" x2="402" y2="696"/>
      <line x1="364" y1="523" x2="402" y2="523"/>
      <line x1="209" y1="581" x2="402" y2="581"/>
      <line x1="364" y1="638" x2="402" y2="638"/>
      <line x1="209" y1="696" x2="402" y2="696"/>
      <line x1="802" y1="373" x2="802" y2="621"/>
      <line x1="802" y1="373" x2="827" y2="373"/>
      <line x1="802" y1="435" x2="996" y2="435"/>
      <line x1="802" y1="498" x2="827" y2="498"/>
      <line x1="802" y1="559" x2="996" y2="559"/>
      <line x1="802" y1="621" x2="827" y2="621"/>
      <line x1="803" y1="77" x2="803" y2="264"/>
      <line x1="803" y1="77" x2="828" y2="77"/>
      <line x1="803" y1="139" x2="997" y2="139"/>
      <line x1="803" y1="201" x2="828" y2="201"/>
      <line x1="803" y1="264" x2="997" y2="264"/>
    </g>
    <g fill="#d6d6d6">
      <circle cx="376" cy="84" r="7"/><circle cx="207" cy="139" r="7"/><circle cx="376" cy="205" r="7"/><circle cx="207" cy="278" r="7"/><circle cx="376" cy="328" r="7"/>
      <circle cx="364" cy="523" r="7"/><circle cx="209" cy="581" r="7"/><circle cx="364" cy="638" r="7"/><circle cx="209" cy="696" r="7"/>
      <circle cx="827" cy="373" r="7"/><circle cx="996" cy="435" r="7"/><circle cx="827" cy="498" r="7"/><circle cx="996" cy="559" r="7"/><circle cx="827" cy="621" r="7"/>
      <circle cx="828" cy="77" r="7"/><circle cx="997" cy="139" r="7"/><circle cx="828" cy="201" r="7"/><circle cx="997" cy="264" r="7"/>
    </g>
    <g fill="var(--summer)"><circle cx="401" cy="84" r="4.5"/><circle cx="401" cy="139" r="4.5"/><circle cx="401" cy="205" r="4.5"/><circle cx="401" cy="278" r="4.5"/><circle cx="401" cy="328" r="4.5"/></g>
    <g fill="var(--fall)"><circle cx="402" cy="523" r="4.5"/><circle cx="402" cy="581" r="4.5"/><circle cx="402" cy="638" r="4.5"/><circle cx="402" cy="696" r="4.5"/></g>
    <g fill="var(--winter)"><circle cx="802" cy="373" r="4.5"/><circle cx="802" cy="435" r="4.5"/><circle cx="802" cy="498" r="4.5"/><circle cx="802" cy="559" r="4.5"/><circle cx="802" cy="621" r="4.5"/></g>
    <g fill="var(--spring)"><circle cx="803" cy="77" r="4.5"/><circle cx="803" cy="139" r="4.5"/><circle cx="803" cy="201" r="4.5"/><circle cx="803" cy="264" r="4.5"/></g>

    <g fill="none" stroke="var(--curve)" stroke-linecap="round">
      <path d="M402,436 C405,450 409,458 413,462" stroke-width="1.5"/>
      <path d="M413,462 C430,495 455,515 490,510" stroke-width="8"/>
      <path d="M490,510 C540,500 600,460 653,378 L766,191" stroke-width="10"/>
      <path d="M766,191 L781,163" stroke-width="1.5"/>
    </g>

    <g class="marker summer-marker" transform="translate(413,462)">
      <circle r="20" fill="#fff" stroke="#ddd"/><circle r="17" fill="#555"/>
      <g stroke="#fff" stroke-width="1.5" fill="none">
        <circle r="5"/>
        <path d="M0,-12V-8M0,8V12M-12,0H-8M8,0H12M-8.5,-8.5L-5.7,-5.7M5.7,5.7L8.5,8.5M-8.5,8.5L-5.7,5.7M5.7,-5.7L8.5,-8.5"/>
      </g>
    </g>
    <g class="marker fall-marker" transform="translate(490,510)">
      <circle r="20" fill="#fff" stroke="#ddd"/><circle r="17" fill="#555"/>
      <path fill="#fff" d="M0,-12 L2.5,-6 L6,-8 L5,-2 L11,-4 L8,1 L10,3 L3,6 L4,8 L0.8,7 L0.8,12 L-0.8,12 L-0.8,7 L-4,8 L-3,6 L-10,3 L-8,1 L-11,-4 L-5,-2 L-6,-8 L-2.5,-6 Z"/>
    </g>
    <g class="marker winter-marker" transform="translate(653,378)">
      <circle r="20" fill="#fff" stroke="#ddd"/><circle r="17" fill="#555"/>
      <g stroke="#fff" stroke-width="1.5" stroke-linecap="round" fill="none">
        <path d="M0,-11V11M-9.5,-5.5L9.5,5.5M-9.5,5.5L9.5,-5.5"/>
        <path d="M-3,-9L0,-6L3,-9M-3,9L0,6L3,9M-9.3,-1.7L-5.2,-3L-6.3,-7.2M9.3,1.7L5.2,3L6.3,7.2M-9.3,1.7L-5.2,3L-6.3,7.2M9.3,-1.7L5.2,-3L6.3,-7.2"/>
      </g>
    </g>
    <g class="marker spring-marker" transform="translate(766,191)">
      <circle r="20" fill="#fff" stroke="#ddd"/><circle r="17" fill="#555"/>
      <g stroke="#fff" stroke-width="1.5" fill="none" stroke-linecap="round">
        <path d="M0,-12 C8,-6 8,4 0,9 C-8,4 -8,-6 0,-12Z"/>
        <path d="M0,-8V13M0,-2L-4,-5M0,-2L4,-5M0,3L-5,-1M0,3L5,-1"/>
      </g>
    </g>
  </svg>

  <!-- Summer -->
  <div class="card summer" style="left:220px;top:43px;min-height:76px"><div class="card-head">Transition</div>
    <ul><li>RO Transition from Reed &amp; Lina</li><li>Start CR Office Initiative</li><li>Tactical Ops transition from Reed</li><li>Formalize Exec Team</li></ul></div>
  <div class="card summer" style="left:51px;top:98px;min-height:88px"><div class="card-head">Biz Architecture</div>
    <ul><li>Independent Financial Audit</li><li>Organizational Audit - Structure</li><li>Organizational Audit - People</li><li>XF Framework - ESU</li><li>Defined Utilization, Realization, Availability</li></ul></div>
  <div class="card summer" style="left:220px;top:158px;min-height:93px"><div class="card-head">Strategy</div>
    <ul><li>Effective Strategy Meeting</li><li>Strategic Themes 2018 - 2020: Stablize, Accelerate, Surge</li><li>Business Drivers: Drive Revenue, Improve Marlowbend Experience, Increase Brand Awareness</li></ul></div>
  <div class="card summer" style="left:51px;top:240px;min-height:76px"><div class="card-head">Sales</div>
    <ul><li>Halvern Account Transition</li><li>Tavenor Account Transition</li><li>2 year Managed Services Engagement Model</li></ul></div>
  <div class="card summer" style="left:220px;top:306px;min-height:44px"><div class="card-head">Revenue / EBITA</div>
    <ul><li>TBD</li></ul></div>
  <div class="season summer" style="left:349px;top:368px;width:98px;height:61px"><span class="name">Summer</span><span class="quarter">Q3 2018</span><span class="theme">Assessment</span></div>

  <!-- Fall -->
  <div class="card fall" style="left:60px;top:507px;width:149px;min-height:147px"><div class="card-head">Biz Architecture</div>
    <ul><li>XF Framework - Functional Meetings &amp; Scrum of Scrums</li><li>Structured Reorg</li><li>Implemented Reorg</li><li>Quarterly Org Iteration cadence</li><li>Defined Key Hire Plan</li><li>CR Office Operational</li><li>Time Accountability</li><li>Tools ReConfig</li><li>Org Structure v1</li></ul></div>
  <div class="card fall" style="left:237px;top:502px;width:127px;min-height:43px"><div class="card-head">Strategy</div>
    <ul><li>Internal QBR Accountability</li></ul></div>
  <div class="card fall" style="left:237px;top:614px;width:127px;min-height:48px"><div class="card-head">Sales</div>
    <ul><li>Quillmere QBR</li><li>Halvern QBR</li></ul></div>
  <div class="card fall" style="left:60px;top:675px;width:149px;min-height:42px"><div class="card-head">Revenue / EBITA</div>
    <ul><li>TBD</li></ul></div>
  <div class="season fall" style="left:446px;top:536px;width:93px;height:60px"><span class="name">Fall</span><span class="quarter">Q4 2018</span><span class="theme">Stablize</span></div>

  <!-- Winter -->
  <div class="card winter" style="left:827px;top:336px;min-height:75px"><div class="card-head">Biz Architecture</div>
    <ul><li>XF Framework - Progress Demos</li><li>Org Structure - COE's</li><li>Stablize Accounting &amp; Finance</li><li>Exec Hiring Process</li></ul></div>
  <div class="card winter" style="left:996px;top:406px;min-height:60px"><div class="card-head">Key Hires</div>
    <ul><li>Controller</li><li>Director CX</li></ul></div>
  <div class="card winter" style="left:827px;top:469px;min-height:57px"><div class="card-head">Strategy</div>
    <ul><li>Founders removed from front line activity</li><li>Marlowbend QBR - Goal Setting &amp; Tracking</li></ul></div>
  <div class="card winter" style="left:996px;top:536px;min-height:49px"><div class="card-head">Sales</div>
    <ul><li>Tavenor QBR</li><li>Halvern QBR</li></ul></div>
  <div class="card winter" style="left:827px;top:597px;min-height:49px"><div class="card-head">Revenue / EBITA</div>
    <ul><li>TBD</li></ul></div>
  <div class="season winter" style="left:687px;top:350px;width:96px;height:61px"><span class="name">Winter</span><span class="quarter">Q1 2018</span><span class="theme">Stratactical</span></div>

  <!-- Spring -->
  <div class="card spring" style="left:828px;top:39px;min-height:75px"><div class="card-head">Biz Architecture</div>
    <ul><li>Tiered Pricing Pre-Paid Engagement Model</li><li>XF Framework - Ideation Board</li><li>Consulting Levels &amp; Salary Bands</li><li>Roles &amp; Responsibilities</li></ul></div>
  <div class="card spring" style="left:997px;top:91px;min-height:96px"><div class="card-head">Key Hires</div>
    <ul><li>Interim HR</li><li>Provisional Client Partner</li><li>Acting Director 1</li><li>Acting Director 2</li><li>Client Partner 1</li><li>Sales Exec 1</li></ul></div>
  <div class="card spring" style="left:828px;top:165px;min-height:73px"><div class="card-head">Sales</div>
    <ul><li>Opened BrightPane Door</li><li>Flipped focus from operationaly run company to sales/marketing driven org</li><li>Pellund Direct</li></ul></div>
  <div class="card spring" style="left:997px;top:242px;min-height:43px"><div class="card-head">Revenue / EBITA</div>
    <ul><li>TBD</li></ul></div>
  <div class="season spring" style="left:652px;top:160px;width:87px;height:60px"><span class="name">Spring</span><span class="quarter">Q2 2018</span><span class="theme">Strategic</span></div>
</div>
</body>
</html>
```